Veltrano.co - Polar Expeditions Specialists

We need a modern, visually striking business card for Veltrano.co, a company specialized in selling expedition cruises to the most remote regions on Earth, with a focus on the Arctic and Antarctica. The design should instantly communicate that the cardholder is an expert in polar travel. Use clean, premium aesthetics with cool tones like icy blue and white, possibly incorporating polar imagery (ice, glaciers, penguins, etc.)

Attached the logo

Contact Information for Business Card

Feels high-end and trustworthy.. Visually memorable — encourages people to keep it

Colors
0054AA
0677BA
7BADD7
CADEEF
E8F1F8

Requirements
Must have
• ice, glaciers, penguins, montains
Nice to have
• modern, transparente,

```html
<!DOCTYPE html>
<html lang="en">
<head>
<meta charset="utf-8">
<title>Veltrano.co – Business Card</title>
<link rel="stylesheet" href="https://fonts.googleapis.com/css2?family=Poppins:wght@500;700&family=Inter:wght@400;500;600&display=swap">
<style>
  :root {
    --backdrop: #777777;
    --navy-deep: #1c2036;
    --navy: #1a2440;
    --navy-soft: #28304a;
    --white: #ffffff;
    --brand-blue: #0677BA;
    --accent-blue: #1173bd;
    --title-blue: #7B9ED8;
    --ink: #3d3d3d;
    --ink-soft: #4a4a4a;
    --rule: #6b6b6b;
  }
  * { box-sizing: border-box; margin: 0; padding: 0; }
  html, body { width: 1200px; height: 1200px; overflow: hidden; }
  body { background: var(--backdrop); position: relative; font-family: "Inter", sans-serif; }

  .card {
    position: absolute;
    left: 179px;
    width: 861px;
    height: 496px;
    box-shadow: 0 14px 26px rgba(0,0,0,0.35);
    overflow: hidden;
  }

  /* Front */
  .card-front { top: 84px; }
  .front-scene {
    position: absolute; inset: 0;
    background:
      radial-gradient(ellipse 70% 40% at 40% 60%, rgba(60,66,92,0.55), transparent 70%),
      linear-gradient(180deg, var(--navy-deep) 0%, var(--navy) 45%, var(--navy-soft) 70%, var(--navy) 100%);
  }
  .front-brand {
    position: absolute; left: 0; right: 0; top: 220px;
    display: flex; align-items: center; justify-content: center; gap: 20px;
  }
  .brand-dot {
    width: 64px; height: 64px; border-radius: 50%;
    background: var(--white);
  }
  .brand-dot.is-blue { background: var(--brand-blue); }
  .brand-name {
    font-family: "Poppins", sans-serif; font-weight: 700;
    font-size: 50px; line-height: 1; color: var(--white);
  }
  .brand-tagline {
    font-family: "Poppins", sans-serif; font-weight: 500;
    font-size: 17px; color: var(--white); margin-top: 8px; letter-spacing: 0.2px;
  }

  /* Back */
  .card-back { top: 622px; background: var(--white); }
  .back-brand {
    position: absolute; left: 82px; top: 100px;
    display: flex; align-items: center; gap: 22px;
  }
  .back-brand .brand-name { color: var(--brand-blue); }
  .back-brand .brand-tagline { color: var(--brand-blue); font-size: 15.5px; }

  .holder { position: absolute; right: 71px; top: 240px; text-align: right; }
  .holder-name {
    font-weight: 600; font-size: 26px; letter-spacing: 1.2px; color: var(--ink);
  }
  .holder-title {
    font-weight: 400; font-size: 23px; letter-spacing: 1px; color: var(--title-blue); margin-top: 6px;
  }
  .divider {
    position: absolute; left: 81px; width: 708px; top: 316px;
    height: 1px; background: var(--rule);
  }
  .contacts { position: absolute; left: 82px; top: 326px; list-style: none; }
  .contacts li {
    display: flex; align-items: center; gap: 12px;
    height: 31.5px; font-size: 20px; letter-spacing: 3px; color: var(--ink-soft);
  }
  .contacts svg { width: 24px; height: 24px; flex: none; }
  .address {
    position: absolute; right: 71px; top: 330px; text-align: right;
    font-style: normal; font-size: 20px; letter-spacing: 3px; color: var(--ink-soft);
    line-height: 31.5px;
  }
  .base-band {
    position: absolute; left: 0; right: 0; bottom: 0; height: 11px;
    background: var(--accent-blue);
  }
</style>
</head>
<body>

<section class="card card-front">
  <div class="front-scene" role="img" aria-label="Dimmed photograph of glaciers and icy mountains under a dark navy overlay"></div>
  <div class="front-brand">
    <span class="brand-dot"></span>
    <div>
      <div class="brand-name">Veltrano.co</div>
      <div class="brand-tagline">Polar Expeditions Specialists</div>
    </div>
  </div>
</section>

<section class="card card-back">
  <div class="back-brand">
    <span class="brand-dot is-blue"></span>
    <div>
      <div class="brand-name">Veltrano.co</div>
      <div class="brand-tagline">Polar Expeditions Specialists</div>
    </div>
  </div>

  <div class="holder">
    <div class="holder-name">DANIEL HARPER</div>
    <div class="holder-title">President/Owner</div>
  </div>

  <div class="divider"></div>

  <ul class="contacts">
    <li>
      <svg viewBox="0 0 24 24" aria-hidden="true"><path fill="#1173bd" d="M6.6 2.5l3 3.4-1.8 2.6c1.2 2.6 3.2 4.6 5.8 5.8l2.6-1.8 3.4 3-1.7 3.3c-8.2-.4-14.4-6.6-14.8-14.8z"/><path d="M14 3.5a7 7 0 0 1 6.5 6.5M14 7a3.5 3.5 0 0 1 3 3" stroke="#1173bd" stroke-width="1.8" fill="none" stroke-linecap="round"/></svg>
      <span>413-555-0142</span>
    </li>
    <li>
      <svg viewBox="0 0 24 24" aria-hidden="true"><rect x="2" y="5" width="20" height="14" fill="#1173bd"/><path d="M2.5 5.5L12 13l9.5-7.5M2.5 18.5l7-6.5M21.5 18.5l-7-6.5" stroke="#fff" stroke-width="1.4" fill="none"/></svg>
      <span>email@yoursite.com</span>
    </li>
    <li>
      <svg viewBox="0 0 24 24" aria-hidden="true"><circle cx="12" cy="12" r="10" fill="#1173bd"/><path d="M7 6c2 1 1 3 3 4s0 3 2 4 0 3 1 5M15 4c0 2 2 2 3 4s3 1 3 3" stroke="#fff" stroke-width="1.6" fill="none"/></svg>
      <span>yourwebsite.com</span>
    </li>
  </ul>

  <address class="address">
    Anywhere Street<br>
    Any City, 758785<br>
    United States
  </address>

  <div class="base-band"></div>
</section>

</body>
</html>
```